Tech business card design

We need an amazing business card design for our new business 'Pexla' a marketing tech startup based in Sydney, Australia. We provide an online marketplace for businesses to search and buy advertising media, connect with service providers and learn more about marketing. We wish to communicate 'cool tech', reliability and professionalism and design based around our logo.

Target Market(s)

Business Owners

Contact Information for Business Card

Name
Position
Email Address
Website
Phone Number

Font styles to use
Other font styles liked:
• Avenir & Avenir Next

Colors

Designer to choose colors to be used in the design.

```html
<!DOCTYPE html>
<html lang="en">
<head>
<meta charset="utf-8">
<title>Pexla Business Card</title>
<link rel="stylesheet" href="https://fonts.googleapis.com/css2?family=Nunito+Sans:wght@400;700;800&display=swap">
<style>
  :root {
    --backdrop: #262626;
    --navy: #171d45;
    --card-grey: #808084;
    --back-grey: #6e6e72;
    --white: #ffffff;
    --logo-faint: #6a6c8c;
  }
  * { box-sizing: border-box; margin: 0; padding: 0; }
  html, body {
    width: 1200px; height: 900px; overflow: hidden;
    background: var(--backdrop);
    font-family: "Nunito Sans", "Avenir Next", Avenir, sans-serif;
  }
  .card {
    position: absolute;
    width: 620px; height: 354px;
    border-radius: 20px;
    overflow: hidden;
    box-shadow: 0 14px 30px rgba(0,0,0,0.5);
  }
  .card-front { left: 120px; top: 70px; background: var(--white); }
  .card-back { left: 460px; top: 486px; background: var(--back-grey); }
  .front-field {
    position: absolute; left: 0; right: 0; top: 150px; bottom: 0;
    background: linear-gradient(100deg, var(--navy) 0%, var(--navy) 40%, var(--card-grey) 72%, var(--card-grey) 100%);
  }
  .brand-name {
    position: absolute;
    font-weight: 800;
    color: var(--navy);
    letter-spacing: -2px;
    line-height: 1;
  }
  .card-front .brand-name { right: 40px; top: 26px; font-size: 84px; }
  .card-back .brand-name {
    left: 0; right: 0; top: 104px;
    text-align: center;
    font-size: 150px;
    color: var(--logo-faint);
  }
  .holder {
    position: absolute; left: 34px; top: 220px;
    color: var(--white);
  }
  .holder-name { font-weight: 800; font-size: 19px; letter-spacing: 0.5px; }
  .holder-role { font-weight: 700; font-size: 14px; margin-left: 12px; }
  .contact-list {
    position: absolute; left: 34px; top: 282px;
    list-style: none; color: var(--white); font-size: 15px;
  }
  .contact-list li { display: flex; align-items: center; gap: 6px; height: 21px; }
  .contact-list svg { width: 12px; height: 12px; fill: var(--white); }
  .address {
    position: absolute; right: 28px; top: 170px;
    text-align: right; color: var(--white); font-size: 15px; line-height: 1.25;
  }
</style>
</head>
<body>
  <section class="card card-front">
    <div class="front-field" role="img" aria-label="Decorative navy and silver sweeping band"></div>
    <div class="brand-name">pexla</div>
    <div class="address">
      <p>Street Name, City Name</p>
      <p>Zipcode:012345</p>
    </div>
    <div class="holder">
      <p class="holder-name">ALEX MORAN</p>
      <p class="holder-role">Position</p>
    </div>
    <ul class="contact-list">
      <li><svg viewBox="0 0 24 24"><path d="M6.6 10.8a15 15 0 0 0 6.6 6.6l2.2-2.2c.3-.3.7-.4 1-.2 1.1.4 2.3.6 3.6.6.6 0 1 .4 1 1V20c0 .6-.4 1-1 1A17 17 0 0 1 3 4c0-.6.4-1 1-1h3.5c.6 0 1 .4 1 1 0 1.3.2 2.5.6 3.6.1.3 0 .7-.2 1z"/></svg>012-345-6789</li>
      <li><svg viewBox="0 0 24 24"><path d="M2 5h20v14H2z M4 7v.5l8 5 8-5V7z" fill-rule="evenodd"/></svg>info@pexla.com</li>
      <li><svg viewBox="0 0 24 24"><circle cx="12" cy="12" r="9" fill="none" stroke="#fff" stroke-width="2"/><path d="M3 12h18M12 3c3 3 3 15 0 18M12 3c-3 3-3 15 0 18" fill="none" stroke="#fff" stroke-width="1.6"/></svg>www.pexla.com</li>
    </ul>
  </section>

  <section class="card card-back">
    <div class="brand-name">pexla</div>
  </section>
</body>
</html>
```